Need a business card design for a residential architect.

You can get a sense of his work at www.tberlove.com

Would like a consistent look and feel between business card and website
.

Target Market(s)

Residential homeowners builders

Industry/Entity Type

Residential

Contact Information for Business Card

Dale Morrick
Principle
Morrick Architecture
418 Kestrel Lane
Harlow Springs, CA 94071

dale@tberlove.com

tberlove.com
phone: 650-555-2716
Fax: 650-555-8043

Font styles to use
Sans Serif

Requirements
Must have
• Details above
Nice to have
• Would like a consistent look and feel between business card and website
Should not have
• None

```html
<!DOCTYPE html>
<html lang="en">
<head>
<meta charset="utf-8">
<title>Morrick Architecture — Business Card</title>
<link href="https://fonts.googleapis.com/css2?family=Cormorant+SC:wght@400;500&family=Jost:wght@400&display=swap" rel="stylesheet">
<style>
  :root {
    --backdrop: #2b2b2b;
    --card-white: #ffffff;
    --card-grey: #6d6d6d;
    --ink: #5c5c5c;
    --ink-soft: #7a7a7a;
    --divider: #e4e4e4;
    --rule-white: #ffffff;
  }
  * { box-sizing: border-box; margin: 0; padding: 0; }
  html, body {
    width: 1200px; height: 900px; overflow: hidden;
    background: var(--backdrop);
  }
  .canvas {
    position: relative; width: 1200px; height: 900px;
    display: flex; flex-direction: column; align-items: center; justify-content: center; gap: 56px;
  }
  .card {
    position: relative; width: 630px; height: 360px;
    box-shadow: 0 18px 40px rgba(0,0,0,.45);
    overflow: hidden;
  }

  /* Front */
  .card--front { background: var(--card-white); color: var(--ink); }
  .card__divider {
    position: absolute; left: 292px; top: 0; bottom: 0; width: 1px;
    background: var(--divider);
  }
  .wordmark {
    font-family: "Jost", sans-serif; font-weight: 400;
    text-transform: uppercase; text-align: center; line-height: 1.1;
  }
  .card--front .wordmark {
    position: absolute; left: 0; width: 292px; top: 160px;
    color: var(--ink); font-size: 26px; letter-spacing: 2px;
  }
  .wordmark__line2 { display: block; font-size: .52em; letter-spacing: .55em; margin-top: 4px; }
  .person {
    position: absolute; right: 48px; top: 36px; text-align: right;
  }
  .person__name {
    font-family: "Cormorant SC", serif; font-weight: 500;
    font-size: 19px; letter-spacing: 1.5px; color: var(--ink-soft);
  }
  .person__title {
    font-family: "Jost", sans-serif; font-size: 12px; color: var(--ink-soft);
  }
  .contacts {
    position: absolute; left: 322px; top: 150px; list-style: none;
    font-family: "Jost", sans-serif; font-size: 13.5px; color: var(--ink);
  }
  .contacts li { display: flex; align-items: center; gap: 14px; height: 24px; white-space: nowrap; }
  .contacts svg { width: 13px; height: 13px; fill: var(--ink); flex: none; }

  /* Back */
  .card--back { background: var(--card-grey); }
  .card__rule {
    position: absolute; left: 0; right: 0; height: 3px; background: var(--rule-white);
  }
  .card__rule--top { top: 112px; }
  .card__rule--bottom { top: 246px; }
  .card--back .wordmark {
    position: absolute; left: 0; right: 0; top: 148px;
    color: var(--rule-white); font-size: 38px; letter-spacing: 3px;
  }
</style>
</head>
<body>
<main class="canvas">

  <section class="card card--front" aria-label="Business card front">
    <div class="wordmark">Morrick<span class="wordmark__line2">Architecture</span></div>
    <div class="card__divider"></div>
    <div class="person">
      <div class="person__name">Dale Morrick</div>
      <div class="person__title">Principle</div>
    </div>
    <ul class="contacts">
      <li>
        <svg viewBox="0 0 12 12" aria-hidden="true"><path d="M6 0a4 4 0 0 0-4 4c0 3 4 8 4 8s4-5 4-8a4 4 0 0 0-4-4zm0 5.6A1.6 1.6 0 1 1 6 2.4a1.6 1.6 0 0 1 0 3.2z"/></svg>
        418 Kestrel Lane Harlow Springs, CA 94071
      </li>
      <li>
        <svg viewBox="0 0 12 12" aria-hidden="true"><path d="M0 2h12v8H0zm1 1.2V9h10V3.2L6 6.6z"/></svg>
        dale@tberlove.com
      </li>
      <li>
        <svg viewBox="0 0 12 12" aria-hidden="true"><path d="M6 0a6 6 0 1 0 0 12A6 6 0 0 0 6 0zm0 1c.8 0 1.6 1.8 1.8 4.5H4.2C4.4 2.8 5.2 1 6 1zM1 6.5h2.2c.1 1.6.4 3 .9 4A5 5 0 0 1 1 6.5zm0-1a5 5 0 0 1 3.1-4c-.5 1-.8 2.4-.9 4zm5 5.5c-.8 0-1.6-1.8-1.8-4.5h3.6C7.6 9.2 6.8 11 6 11zm1.9-.5c.5-1 .8-2.4.9-4H11a5 5 0 0 1-3.1 4zm.9-5c-.1-1.6-.4-3-.9-4A5 5 0 0 1 11 5.5z"/></svg>
        tberlove.com
      </li>
      <li>
        <svg viewBox="0 0 12 12" aria-hidden="true"><path d="M2.5 0l2 2.8-1.2 1.5a7 7 0 0 0 4.4 4.4l1.5-1.2 2.8 2-1.5 2.5C4.5 11.7.3 7.5 0 1.5z"/></svg>
        650-555-2716
      </li>
      <li>
        <svg viewBox="0 0 12 12" aria-hidden="true"><path d="M3 0h5v3H3zM1 4h10v6H1zm2 1v1h2V5zm4 0v1h2V5zM3 10.5h6V12H3z"/></svg>
        650-555-8043
      </li>
    </ul>
  </section>

  <section class="card card--back" aria-label="Business card back">
    <div class="card__rule card__rule--top"></div>
    <div class="wordmark">Morrick<span class="wordmark__line2">Architecture</span></div>
    <div class="card__rule card__rule--bottom"></div>
  </section>

</main>
</body>
</html>
```